Brochure design for International Beauty Trade Show

I neee a tri-fold company products' brochure to distribute to customers at an international trade show coming soon. We have 4 main product categories- hair and skincare, facial care, Body and bath and massage oil.
The brochure needs to include at least 2 photos of the main products of each category, benefits, call to action and our company contact info ( website and phone number).

Target Market(s)

Educated and high income earners looking for all-natural,pure, 100 organic products for their beauty and personal care needs. Our products cross all racial groups/demographics and suitable for all skin types

Industry/Entity Type

Hair And Beauty

Font styles to use
Serif

Colors

Designer to choose colors to be used in the design.

Requirements
Must have
• The design must stand out as pure and luxury and at the same time be inclusive using our logo design colors- orange and blue. Also, the content must be easy to read and captivating.
• Finally if using women pictures, please include Black, white, Asian and Latina to reflect the fact that our products are suitable for all skin types.
Nice to have
• Design the brochure such that it could be printed as a poster-banner ad.
Should not have
• Cookie cutter designs are not welcome

```html
<!DOCTYPE html>
<html lang="en">
<head>
<meta charset="utf-8">
<title>Solenne Botanics – Tri-fold Brochure</title>
<link href="https://fonts.googleapis.com/css2?family=Lato:wght@300;400;700;900&display=swap" rel="stylesheet">
<style>
  :root {
    --brand-orange: #ee7526;
    --brand-blue: #1a8ccd;
    --ink: #3a3a3a;
    --copy: #6b6b6b;
    --panel: #ffffff;
    --panel-shade: #f1f1f1;
    --stage: #e4e4e4;
    --rule: #d6d6d6;
    --night: #1b1b1b;
  }
  * { box-sizing: border-box; margin: 0; padding: 0; }
  html, body { width: 1200px; height: 1000px; overflow: hidden; }
  body {
    background: radial-gradient(ellipse at center, #f4f4f4 0%, var(--stage) 75%);
    font-family: "Lato", Arial, sans-serif;
    color: var(--ink);
    position: relative;
  }
  .brochure {
    position: absolute; top: 200px; left: 80px;
    display: flex; gap: 40px;
  }
  .inside-spread {
    display: flex; width: 780px; height: 600px;
    box-shadow: 0 10px 30px rgba(0,0,0,.18);
  }
  .panel {
    width: 260px; height: 600px; position: relative;
    background: linear-gradient(180deg, var(--panel) 55%, var(--panel-shade) 100%);
    overflow: hidden;
  }
  .panel + .panel { border-left: 1px solid #e6e6e6; }
  .photo { display: block; width: 100%; }
  .section { padding: 0 22px; }
  .section-title {
    font-weight: 700; font-size: 17px; color: var(--ink);
    display: flex; align-items: center; gap: 8px; margin: 22px 0 12px;
  }
  .section-title::before {
    content: ""; width: 6px; height: 22px; background: var(--bar, var(--brand-blue));
  }
  .section-title.is-orange { --bar: var(--brand-orange); }
  .benefits { list-style: none; }
  .benefits li {
    font-size: 12.5px; font-weight: 300; color: var(--copy);
    line-height: 1.75; padding-left: 16px; position: relative; white-space: nowrap;
  }
  .benefits li::before {
    content: ""; position: absolute; left: 3px; top: 9px;
    width: 4px; height: 4px; border-radius: 50%; background: var(--copy);
  }
  .product-row {
    display: flex; justify-content: center; align-items: flex-end; gap: 12px; margin-top: 14px;
  }
  .product-shot { display: block; border-radius: 4px; }
  .divider { border: 0; border-top: 1px solid var(--rule); margin: 16px 22px 0; }

  .contact-band {
    position: absolute; left: 0; bottom: 0; width: 100%; height: 150px;
    background: linear-gradient(135deg, #151515 0%, var(--night) 60%, #3a2e22 100%);
    color: #fff; padding: 18px 22px;
  }
  .cta {
    font-size: 15px; font-weight: 700; color: var(--brand-orange); letter-spacing: .3px;
  }
  .cta-note {
    font-size: 11.5px; font-weight: 300; color: #cfcfcf; margin: 4px 0 14px; line-height: 1.5;
  }
  .contact-line {
    display: flex; align-items: center; gap: 8px;
    font-size: 12.5px; font-weight: 400; color: #ffffff; line-height: 1.9;
  }
  .contact-line svg { flex: none; }

  .cover {
    width: 260px; height: 600px; background: var(--panel);
    box-shadow: 0 10px 30px rgba(0,0,0,.18);
    position: relative; overflow: hidden;
    display: flex; flex-direction: column; align-items: center;
  }
  .brand-mark { margin-top: 56px; display: flex; align-items: center; gap: 10px; }
  .brand-mark .dot { width: 30px; height: 30px; border-radius: 50%; background: var(--brand-orange); }
  .brand-mark .name { font-size: 30px; font-weight: 900; color: var(--brand-orange); letter-spacing: .5px; }
  .tagline { text-align: center; margin-top: 60px; }
  .tagline .lead { font-size: 20px; font-weight: 700; color: var(--brand-blue); letter-spacing: .3px; }
  .tagline .sub { font-size: 18px; font-weight: 400; color: var(--brand-orange); margin-top: 2px; }
  .cover-photo { position: absolute; left: 0; bottom: 0; width: 100%; height: 300px; }
</style>
</head>
<body>
<main class="brochure">
  <section class="inside-spread">
    <article class="panel panel-hair">
      <svg class="photo" width="260" height="130" role="img" aria-label="Spa scene with candles, stones, bamboo, carrots and a carrot oil bottle">
        <defs><linearGradient id="spaTone" x1="0" y1="0" x2="1" y2="1">
          <stop offset="0" stop-color="#e9e6e0"/><stop offset=".6" stop-color="#8f8a84"/><stop offset="1" stop-color="#3c3a38"/></linearGradient></defs>
        <rect width="260" height="130" fill="url(#spaTone)"/>
      </svg>
      <div class="section">
        <h2 class="section-title">Hair &amp; Skincare</h2>
        <ul class="benefits">
          <li>Anti-Aging, remove wrinkles</li>
          <li>Natural moisturizer</li>
          <li>Heal damaged hair or sensitive scalp</li>
          <li>Soften curly and frizzy hair</li>
          <li>Reduce sebum secretion</li>
          <li>Tone, soothe and restore luster</li>
          <li>Restore fair complexion</li>
        </ul>
        <div class="product-row">
          <svg class="product-shot" width="90" height="140" role="img" aria-label="Tall amber hair oil bottles with gold pump caps">
            <defs><linearGradient id="oilTone" x1="0" y1="0" x2="0" y2="1">
              <stop offset="0" stop-color="#f3ede4"/><stop offset="1" stop-color="#c98b52"/></linearGradient></defs>
            <rect width="90" height="140" rx="4" fill="url(#oilTone)"/>
          </svg>
          <svg class="product-shot" width="90" height="115" role="img" aria-label="Small amber skin oil bottles with gold caps">
            <defs><linearGradient id="oilTone2" x1="0" y1="0" x2="0" y2="1">
              <stop offset="0" stop-color="#f1ebe2"/><stop offset="1" stop-color="#b9773f"/></linearGradient></defs>
            <rect width="90" height="115" rx="4" fill="url(#oilTone2)"/>
          </svg>
        </div>
      </div>
    </article>

    <article class="panel panel-face">
      <div class="section">
        <h2 class="section-title is-orange">Facial Care</h2>
        <ul class="benefits">
          <li>Reduce sebum secretion</li>
          <li>Eliminate toxins &amp; blemishes</li>
          <li>Tighten pores</li>
          <li>Dry pimples</li>
          <li>Remove blackheads</li>
        </ul>
        <div class="product-row">
          <svg class="product-shot" width="90" height="68" role="img" aria-label="White facial cream jar">
            <defs><linearGradient id="faceTone" x1="0" y1="0" x2="0" y2="1">
              <stop offset="0" stop-color="#f2f2ee"/><stop offset="1" stop-color="#cfd3c8"/></linearGradient></defs>
            <rect width="90" height="68" rx="4" fill="url(#faceTone)"/>
          </svg>
          <svg class="product-shot" width="80" height="52" role="img" aria-label="Boxed green facial soap">
            <defs><linearGradient id="soapTone" x1="0" y1="0" x2="1" y2="0">
              <stop offset="0" stop-color="#e4ece0"/><stop offset="1" stop-color="#a9c99e"/></linearGradient></defs>
            <rect width="80" height="52" rx="4" fill="url(#soapTone)"/>
          </svg>
        </div>
      </div>
      <hr class="divider">
      <div class="section">
        <h2 class="section-title">Massage Care</h2>
        <ul class="benefits">
          <li>Relief stress and pain</li>
          <li>Fight muscle contraction/tenderness</li>
          <li>Eliminate stretch marks</li>
          <li>Pure, natural undiluted</li>
        </ul>
        <div class="product-row">
          <svg class="product-shot" width="90" height="62" role="img" aria-label="Dark massage balm jar">
            <defs><linearGradient id="balmTone" x1="0" y1="0" x2="0" y2="1">
              <stop offset="0" stop-color="#5a5862"/><stop offset="1" stop-color="#1e1e24"/></linearGradient></defs>
            <rect width="90" height="62" rx="4" fill="url(#balmTone)"/>
          </svg>
          <svg class="product-shot" width="70" height="96" role="img" aria-label="Massage oil spray bottle with red berries">
            <defs><linearGradient id="sprayTone" x1="0" y1="0" x2="0" y2="1">
              <stop offset="0" stop-color="#ecebee"/><stop offset=".6" stop-color="#6a5a6a"/><stop offset="1" stop-color="#9a3530"/></linearGradient></defs>
            <rect width="70" height="96" rx="4" fill="url(#sprayTone)"/>
          </svg>
        </div>
      </div>
    </article>

    <article class="panel panel-body">
      <svg class="photo" width="260" height="150" role="img" aria-label="Argan soap jars with candles, orange slice and flowers">
        <defs><linearGradient id="bathTone" x1="0" y1="0" x2="1" y2="1">
          <stop offset="0" stop-color="#f5f3ef"/><stop offset=".6" stop-color="#d9d2c6"/><stop offset="1" stop-color="#e9a04e"/></linearGradient></defs>
        <rect width="260" height="150" fill="url(#bathTone)"/>
      </svg>
      <div class="section">
        <h2 class="section-title is-orange">Body &amp; Bath Care</h2>
        <ul class="benefits">
          <li>Purify and disinfect</li>
          <li>Fight acne</li>
          <li>Rejuvenate &amp; hydrate</li>
          <li>Promote healthy looking skin</li>
          <li>Remove dead cells</li>
        </ul>
        <div class="product-row">
          <svg class="product-shot" width="80" height="60" role="img" aria-label="Body scrub jar with red clay">
            <defs><linearGradient id="scrubTone" x1="0" y1="0" x2="1" y2="1">
              <stop offset="0" stop-color="#e6e4e0"/><stop offset="1" stop-color="#c2603e"/></linearGradient></defs>
            <rect width="80" height="60" rx="4" fill="url(#scrubTone)"/>
          </svg>
          <svg class="product-shot" width="70" height="50" role="img" aria-label="Boxed body soap with lemons">
            <defs><linearGradient id="lemonTone" x1="0" y1="0" x2="1" y2="0">
              <stop offset="0" stop-color="#dfe8d6"/><stop offset="1" stop-color="#e6d36a"/></linearGradient></defs>
            <rect width="70" height="50" rx="4" fill="url(#lemonTone)"/>
          </svg>
        </div>
      </div>
      <footer class="contact-band">
        <p class="cta">Order Today &amp; Glow Naturally</p>
        <p class="cta-note">100% organic care for every skin type.</p>
        <p class="contact-line">
          <svg width="14" height="14" viewBox="0 0 24 24" aria-hidden="true"><path fill="#ee7526" d="M6.6 10.8a15 15 0 0 0 6.6 6.6l2.2-2.2c.3-.3.7-.4 1-.2 1.1.4 2.3.6 3.6.6.6 0 1 .4 1 1V20c0 .6-.4 1-1 1A17 17 0 0 1 3 4c0-.6.4-1 1-1h3.5c.6 0 1 .4 1 1 0 1.2.2 2.4.6 3.6.1.3 0 .7-.2 1z"/></svg>
          +1 (555) 214-7730
        </p>
        <p class="contact-line">
          <svg width="14" height="14" viewBox="0 0 24 24" aria-hidden="true"><circle cx="12" cy="12" r="9" fill="none" stroke="#1a8ccd" stroke-width="2"/><path d="M3 12h18M12 3c3 3 3 15 0 18M12 3c-3 3-3 15 0 18" fill="none" stroke="#1a8ccd" stroke-width="1.6"/></svg>
          www.solennebotanics.com
        </p>
      </footer>
    </article>
  </section>

  <section class="cover">
    <div class="brand-mark">
      <span class="dot"></span>
      <span class="name">Solenne</span>
    </div>
    <div class="tagline">
      <p class="lead">NATURAL SOLUTIONS</p>
      <p class="sub">to Forever Beauty</p>
    </div>
    <svg class="cover-photo" width="260" height="300" role="img" aria-label="Four smiling women of different ethnicities in white tops">
      <defs><linearGradient id="peopleTone" x1="0" y1="0" x2="1" y2="1">
        <stop offset="0" stop-color="#f3e2d4"/><stop offset=".45" stop-color="#d2a585"/><stop offset="1" stop-color="#6b4330"/></linearGradient></defs>
      <rect width="260" height="300" fill="url(#peopleTone)"/>
    </svg>
  </section>
</main>
</body>
</html>
```